Brightfield Ventures Inc. Letterhead

Creation of attractive and eye catching letterhead for a business start-up for the construction industry. Letterhead must relate to construction, but avoid standard hammer and tools in the design.

I forgot to add some details, sorry about that. Some pertinent info: Ph: 916-555-0187 brightfieldventures.example 448 Willowmere Ave, Ste 210 Folsom, CA 95999 info@brightfieldventures.example not sure if slogan should be in there" “Connecting construction professionals to create a purpose driven industry.” must be able to be used in word. Thanks!

```html
<!DOCTYPE html>
<html lang="en">
<head>
<meta charset="utf-8">
<title>Brightfield Ventures Inc. Letterhead</title>
<link href="https://fonts.googleapis.com/css2?family=Source+Sans+3:wght@400;600&family=Arimo:wght@700&display=swap" rel="stylesheet">
<style>
  :root {
    --backdrop: #e4e5e7;
    --paper: #ffffff;
    --brand-red: #b5090d;
    --brand-navy: #1c2a5e;
    --ink: #2b2b2b;
    --on-red: #ffffff;
    --signature-tone: #d9d9dc;
  }
  * { box-sizing: border-box; margin: 0; padding: 0; }
  html, body {
    width: 1200px; height: 945px; overflow: hidden;
    background: var(--backdrop);
  }
  .letterhead {
    position: absolute; left: 280px; top: 20px;
    width: 640px; height: 905px;
    background: var(--paper);
    box-shadow: 0 4px 18px rgba(0,0,0,0.12);
    overflow: hidden;
    font-family: "Source Sans 3", "Myriad Pro", sans-serif;
    color: var(--ink);
  }
  .letterhead__band { position: absolute; left: 0; top: 0; width: 640px; height: 180px; }
  .contact {
    position: absolute; right: 38px; top: 22px;
    text-align: right; color: var(--on-red);
    font-size: 10.5px; line-height: 1.45;
  }
  .contact__row { display: flex; justify-content: flex-end; align-items: center; gap: 5px; }
  .contact__row svg { width: 9px; height: 9px; fill: var(--on-red); }
  .contact__address { margin-top: 10px; font-size: 10px; line-height: 1.35; }
  .brand {
    position: absolute; left: 48px; top: 140px;
    display: flex; align-items: center; gap: 8px;
  }
  .brand__mark { width: 16px; height: 16px; background: var(--brand-red); }
  .brand__name {
    font-size: 17px; font-weight: 600; letter-spacing: 0.5px;
    color: var(--brand-navy);
  }
  .letter { position: absolute; left: 54px; top: 222px; width: 530px; }
  .letter__salutation {
    font-family: "Arimo", Arial, sans-serif; font-weight: 700;
    font-size: 15px; margin-bottom: 10px; color: #111;
  }
  .letter__para { font-size: 13.2px; line-height: 1.4; margin-bottom: 18px; }
  .letter__para--indent { padding-left: 36px; }
  .signature {
    position: absolute; left: 62px; top: 770px;
    width: 150px; height: 52px; border-radius: 4px;
    background: linear-gradient(90deg, var(--signature-tone), #eeeef0);
  }
</style>
</head>
<body>
  <main class="letterhead">
    <svg class="letterhead__band" viewBox="0 0 640 180" aria-hidden="true">
      <path d="M0 0 H640 V92 C540 128 420 140 300 128 C190 116 90 108 0 118 Z" fill="var(--brand-red)"/>
      <path d="M0 122 C110 110 230 118 360 134 C250 126 120 124 0 138 Z" fill="var(--brand-red)"/>
      <path d="M0 142 C120 124 240 124 330 136 C230 132 110 136 0 154 Z" fill="var(--brand-navy)"/>
      <path d="M300 140 C420 148 540 136 640 104 V112 C540 146 420 156 300 140 Z" fill="var(--brand-red)"/>
    </svg>

    <div class="contact">
      <div class="contact__row">773-555-0142
        <svg viewBox="0 0 10 10"><path d="M2 0.5 L4 2.5 L3 3.7 C3.6 5 5 6.4 6.3 7 L7.5 6 L9.5 8 L8.3 9.5 C4.5 9.5 0.5 5.5 0.5 1.7 Z"/></svg>
      </div>
      <div class="contact__row">info@brightfieldventures.example
        <svg viewBox="0 0 10 10"><path d="M0.5 2 H9.5 V8 H0.5 Z M1 2.5 L5 5.5 L9 2.5" stroke="#b5090d" stroke-width="0.6"/></svg>
      </div>
      <div class="contact__row">www.brightfieldventures.example
        <svg viewBox="0 0 10 10"><circle cx="5" cy="5" r="4.5"/><path d="M0.5 5 H9.5 M5 0.5 V9.5" stroke="#b5090d" stroke-width="0.6"/></svg>
      </div>
      <div class="contact__address">448 Willowmere Ave, Ste 210,<br>Folsom, CA 95999</div>
    </div>

    <div class="brand">
      <span class="brand__mark"></span>
      <span class="brand__name">Brightfield Ventures Inc.</span>
    </div>

    <article class="letter">
      <p class="letter__salutation">Dear Mr. Harlow,</p>
      <p class="letter__para">Lorem Ipsum is simply dummy text of the printing and typesetting industry. Lorem Ipsum has been the industry's standard dummy text ever since the 1500s, when an unknown printer took a galley of type and scrambled it to make a type specimen book. It has survived not only five centuries, but also the leap into electronic typesetting, remaining essentially unchanged.</p>
      <p class="letter__para letter__para--indent">The standard chunk of Lorem Ipsum used since the 1500s is reproduced below for those interested. Sections 1.10.32 and 1.10.33 from "de Finibus Bonorum et Malorum" by Corvinus are also reproduced in their exact original form, accompanied by English versions from the 1914 translation by H.Ravenstone.</p>
      <p class="letter__para">Lorem Ipsum is simply dummy text of the printing and typesetting industry. Lorem Ipsum has been the industry's standard dummy text ever since the 1500s, when an unknown printer took a galley of type and scrambled it to make a type specimen book. It has survived not only five centuries, but also the leap into electronic typesetting, remaining essentially unchanged. It was popularised in the</p>
      <p class="letter__para letter__para--indent">The standard chunk of Lorem Ipsum used since the 1500s is reproduced below for those interested. Sections 1.10.32 and 1.10.33 from "de Finibus Bonorum et Malorum" by Corvinus are also reproduced in their exact original form, accompanied by English versions from the 1914 translation by H.Ravenstone.</p>
      <p class="letter__para letter__para--indent">The standard chunk of Lorem Ipsum used since the 1500s is reproduced below for those interested. Sections 1.10.32 and 1.10.33 from "de Finibus Bonorum et Malorum" by Corvinus are</p>
    </article>

    <div class="signature" role="img" aria-label="Handwritten signature of the sender"></div>
  </main>
</body>
</html>
```